Lanternfield Drinks business cards

We need a business card design for our new logo. The company is modern, progressive, professional, yet approachable. The key products are ready to drink bottles and cans of coffee based beverages.
These cards will be a critical part of the first impression made by our sales organization, business development team, and all external facing personnel.
Card can be a vertical or horizontal orientation.

Target Market(s)

Customers, suppliers, business partners

Industry/Entity Type

Business

Contact Information for Business Card

Business cards should feature Company Name and Logo.

Font styles to use
Serif

Colors

Designer to choose colors to be used in the design.

Requirements
Must have
• Strong readability of Name, phone #, mobile number and email address.
• Job title, website url, Street Address, and other details can be secondary level readability.
Nice to have
• High impact, simplistic quality design.
• Ok to utilize the 'H in the box' separate from the company name

```html
<!DOCTYPE html>
<html lang="en">
<head>
<meta charset="utf-8">
<title>Lanternfield Drinks – Business Cards</title>
<link href="https://fonts.googleapis.com/css2?family=Lato:wght@400;700&display=swap" rel="stylesheet">
<style>
  :root {
    --backdrop: #777777;
    --card: #000000;
    --accent: #f05a28;
    --accent-warm: #f7941d;
    --text-light: #ffffff;
    --divider: #5a5a5a;
  }
  html, body {
    margin: 0;
    padding: 0;
    width: 1200px;
    height: 900px;
    overflow: hidden;
    background: var(--backdrop);
    font-family: "Lato", sans-serif;
  }
  .canvas {
    position: relative;
    width: 1200px;
    height: 900px;
  }
  .card {
    position: absolute;
    top: 307px;
    height: 270px;
    background: var(--card);
    border-radius: 10px;
  }
  .card--back { left: 150px; width: 437px; }
  .card--front { left: 609px; width: 439px; }

  /* Back side */
  .brand-block {
    position: absolute;
    left: 43px;
    top: 74px;
    width: 140px;
    display: flex;
    align-items: center;
    gap: 10px;
  }
  .brand-block__square {
    width: 18px;
    height: 18px;
    flex: none;
    background: var(--accent);
  }
  .brand-name {
    color: var(--accent);
    font-weight: 700;
    font-size: 17px;
    line-height: 1.15;
    letter-spacing: 0.5px;
    text-transform: uppercase;
    margin: 0;
  }
  .divider {
    position: absolute;
    left: 207px;
    top: 54px;
    width: 1px;
    height: 165px;
    background: var(--divider);
  }
  .person {
    position: absolute;
    left: 225px;
    top: 51px;
  }
  .person__name {
    margin: 0;
    color: var(--accent);
    font-weight: 700;
    font-size: 17.5px;
    line-height: 20px;
  }
  .person__title {
    margin: 0;
    color: var(--accent-warm);
    font-size: 12.5px;
    line-height: 16px;
    text-transform: uppercase;
  }
  .contact-list {
    position: absolute;
    left: 226px;
    top: 97px;
    margin: 0;
    padding: 0;
    list-style: none;
    color: var(--text-light);
    font-size: 12.5px;
  }
  .contact-list li {
    display: flex;
    align-items: flex-start;
    gap: 7px;
    height: 16.5px;
  }
  .contact-list li.contact-list__address {
    margin-top: 8px;
    line-height: 16px;
    height: auto;
  }
  .contact-icon {
    width: 14px;
    height: 14px;
    flex: none;
    margin-top: 1px;
  }

  /* Front side */
  .front-mark {
    position: absolute;
    left: 175px;
    top: 53px;
    width: 86px;
    height: 86px;
    box-sizing: border-box;
    border: 4px solid var(--accent);
  }
  .front-name {
    position: absolute;
    left: 0;
    right: 0;
    top: 158px;
    margin: 0;
    text-align: center;
    color: var(--accent);
    font-weight: 700;
    font-size: 34px;
    line-height: 40px;
    letter-spacing: 1px;
    text-transform: uppercase;
  }
</style>
</head>
<body>
<main class="canvas">

  <section class="card card--back" aria-label="Card back with contact details">
    <div class="brand-block">
      <span class="brand-block__square"></span>
      <p class="brand-name">Lanternfield<br>Drinks</p>
    </div>

    <span class="divider"></span>

    <div class="person">
      <p class="person__name">LORUM SMITH</p>
      <p class="person__title">Managing Director</p>
    </div>

    <ul class="contact-list">
      <li>
        <svg class="contact-icon" viewBox="0 0 14 14" aria-hidden="true"><circle cx="7" cy="7" r="7" fill="var(--accent)"/><path d="M4.5 3.8c.4-.4.9-.3 1.1.1l.6 1.2c.1.3 0 .5-.2.7l-.4.3c.3.8.9 1.4 1.7 1.7l.3-.4c.2-.2.4-.3.7-.2l1.2.6c.4.2.5.7.1 1.1-1.4 1.4-6.5-3.7-5.1-5.1z" fill="#fff"/></svg>
        <span>888 555 4433</span>
      </li>
      <li>
        <svg class="contact-icon" viewBox="0 0 14 14" aria-hidden="true"><circle cx="7" cy="7" r="7" fill="var(--accent)"/><rect x="4.8" y="3.3" width="4.4" height="7.4" rx="0.8" fill="none" stroke="#fff" stroke-width="1"/></svg>
        <span>888 444 0000</span>
      </li>
      <li>
        <svg class="contact-icon" viewBox="0 0 14 14" aria-hidden="true"><circle cx="7" cy="7" r="7" fill="var(--accent)"/><rect x="3.6" y="4.6" width="6.8" height="4.8" fill="#fff"/><path d="M3.6 4.6 7 7.3l3.4-2.7" fill="none" stroke="var(--accent)" stroke-width="0.8"/></svg>
        <span>info@webname.com</span>
      </li>
      <li>
        <svg class="contact-icon" viewBox="0 0 14 14" aria-hidden="true"><circle cx="7" cy="7" r="7" fill="var(--accent)"/><circle cx="7" cy="7" r="3.4" fill="none" stroke="#fff" stroke-width="1"/><path d="M3.6 7h6.8M7 3.6v6.8" stroke="#fff" stroke-width="0.8"/></svg>
        <span>www.webname.com</span>
      </li>
      <li class="contact-list__address">
        <svg class="contact-icon" viewBox="0 0 14 14" aria-hidden="true"><circle cx="7" cy="7" r="7" fill="var(--accent)"/><path d="M7 11c-1.8-2.2-2.7-3.6-2.7-4.8a2.7 2.7 0 0 1 5.4 0C9.7 7.4 8.8 8.8 7 11z" fill="#fff"/><circle cx="7" cy="6.2" r="1" fill="var(--accent)"/></svg>
        <span>421, Address line here,<br>Dummy Code, 45452<br>Country Name</span>
      </li>
    </ul>
  </section>

  <section class="card card--front" aria-label="Card front with company name">
    <span class="front-mark"></span>
    <p class="front-name">Lanternfield Drinks</p>
  </section>

</main>
</body>
</html>
```